Property Investment eBook Cover

I am a long established Australian property investment adviser, analyst and consultant who is now in semi-retired mode and have re-branded to reflect a more casual and personal approach to advising my property investor clients. I am writing a 'revised edition' to a book written in partnership with my father 20 years ago and need an eBook Cover for this new edition. The eBook will be uploaded to all the regular Australian providers (Corvex Slate, Pebble Ureader, Navi, Leafmarta)

The 3 key elements in the book cover are:

Title: The Harvest Rule of Land. The word 'Property' should be larger and more prominent. eg "The Wealth Power of" could be 1/3 the size of "Property" - with both justified left

Edition: Sydney 2021. "Sydney 2021" should be the focus and dominant imagery of the eBook cover and more prominent than the Title or Author

Author: Colin Marwick, The Housing Examiner. The word "Author" should not appear. "The Housing Examiner" should appear underneath Colin Marwick and justified to Colin Marwick, therefore a smaller font.

The cover should be simple, but eye-catching. No property images, more of an abstract background, than a background with an image. Our preferred colour palette is more blues/greens. Prefer SerifFonts

Copy of book published 20 years ago attached for reference only

```html
<!DOCTYPE html>
<html lang="en">
<head>
<meta charset="utf-8">
<title>The Harvest Rule of Land — Colin Marwick</title>
<link rel="stylesheet" href="https://fonts.googleapis.com/css2?family=Alegreya:ital,wght@0,700;0,800;1,400&family=Roboto+Condensed:wght@700&family=Montserrat:wght@300;600&display=swap">
<style>
  :root {
    --deep-blue: #003f6c;
    --mid-blue: #00598a;
    --glow-blue: #0087bd;
    --badge-yellow: #ffff00;
    --badge-gold: #f0dc00;
    --edition-red: #f00000;
    --title-white: #ffffff;
  }
  html, body {
    margin: 0;
    padding: 0;
    width: 750px;
    height: 1200px;
    overflow: hidden;
    background: var(--deep-blue);
  }
  .cover {
    position: relative;
    width: 750px;
    height: 1200px;
    overflow: hidden;
    background: linear-gradient(180deg, var(--mid-blue) 0%, #006b9c 40%, var(--deep-blue) 100%);
  }
  .backdrop, .title-art {
    position: absolute;
    inset: 0;
  }
  .title-serif {
    font-family: "Alegreya", Georgia, serif;
    fill: var(--title-white);
  }
  .title-serif.italic { font-style: italic; font-weight: 400; }
  .title-serif.bold { font-weight: 800; }
  .title-rule {
    stroke: var(--title-white);
    stroke-width: 3;
  }
  .edition {
    font-family: "Roboto Condensed", "Arial Narrow", sans-serif;
    font-weight: 700;
    fill: var(--edition-red);
  }
  .author {
    position: absolute;
    left: 0;
    right: 0;
    top: 1022px;
    text-align: center;
    color: var(--title-white);
    font-family: "Montserrat", Arial, sans-serif;
    transform: translateX(22px);
  }
  .author-name {
    margin: 0;
    font-weight: 600;
    font-size: 52px;
    line-height: 1.05;
    letter-spacing: -0.5px;
  }
  .author-role {
    margin: 4px 0 0;
    font-weight: 300;
    font-size: 29px;
    line-height: 1.1;
  }
</style>
</head>
<body>
<main class="cover">
  <svg class="backdrop" width="750" height="1200" viewBox="0 0 750 1200">
    <defs>
      <radialGradient id="glow-left" cx="0.7" cy="0.55" r="0.6">
        <stop offset="0" stop-color="#0088bf" stop-opacity="0.9"/>
        <stop offset="1" stop-color="#0088bf" stop-opacity="0.15"/>
      </radialGradient>
      <radialGradient id="glow-right" cx="0.3" cy="0.35" r="0.7">
        <stop offset="0" stop-color="#0088bf" stop-opacity="0.75"/>
        <stop offset="1" stop-color="#0088bf" stop-opacity="0.05"/>
      </radialGradient>
      <radialGradient id="badge-fill" cx="0.55" cy="0.55" r="0.5">
        <stop offset="0" stop-color="var(--badge-gold)"/>
        <stop offset="1" stop-color="#fbf000"/>
      </radialGradient>
    </defs>
    <circle cx="-140" cy="470" r="525" fill="url(#glow-left)"/>
    <circle cx="860" cy="560" r="480" fill="url(#glow-right)"/>
    <circle class="badge" cx="113" cy="117" r="202" fill="var(--badge-yellow)"/>
    <circle class="badge-inner" cx="113" cy="117" r="175" fill="url(#badge-fill)"/>
  </svg>

  <svg class="title-art" width="750" height="1200" viewBox="0 0 750 1200" aria-label="Sydney 2021 — The Harvest Rule of Land">
    <defs>
      <filter id="lift" x="-5%" y="-5%" width="110%" height="115%">
        <feDropShadow dx="1.5" dy="2" stdDeviation="1.5" flood-color="#001a33" flood-opacity="0.6"/>
      </filter>
    </defs>

    <g class="edition-badge" transform="rotate(-10 150 120)">
      <text class="edition" x="150" y="158" font-size="102" text-anchor="middle">Sydney</text>
      <text class="edition" x="160" y="246" font-size="118" text-anchor="middle">2021</text>
    </g>

    <g class="title" filter="url(#lift)">
      <text class="title-serif italic" x="324" y="281" font-size="74">The</text>
      <line class="title-rule" x1="430" y1="274" x2="660" y2="274"/>

      <text class="title-serif bold" x="190" y="418" font-size="138" textLength="470" lengthAdjust="spacingAndGlyphs">Harvest</text>
      <line class="title-rule" x1="183" y1="432" x2="660" y2="432"/>

      <text class="title-serif bold" x="186" y="582" font-size="135">Rule</text>
      <text class="title-serif italic" x="498" y="590" font-size="92">of</text>
      <line class="title-rule" x1="183" y1="598" x2="633" y2="598"/>

      <text class="title-serif bold" font-size="400" transform="translate(40 880) scale(0.62 1)">Land</text>
      <line class="title-rule" x1="46" y1="920" x2="594" y2="920"/>
    </g>
  </svg>

  <header class="author">
    <p class="author-name">Colin Marwick</p>
    <p class="author-role">The Housing Examiner</p>
  </header>
</main>
</body>
</html>
```